Wordpress Web Design & Coding for velcorahealth.ca

We need a website for a new investment company that is visually grabbing and vibrant. We would like to see a web page that displays trust, growth and confidence. Needs to be responsive and mobile friendly for all browsers and coded for both Android & IOS.

Open to the number of pages and menu items. I selected 4 but if you feel the layout would work better with less I am open to this. Need to sell the people (management team/related businesses) and then show where the invested money will be going (upcoming projects).

Company Info:

Vel Cora is an investment company put together by a group of seasoned business professionals who have come together to combine decades of success in the real estate development, management, financing and medical services. The company will be a full service company offering turn key solutions for medical professionals.

Vel-Cora will focus on providing a full range of services via a group of distinct companies to deliver newly emerging needs of the medical community. The end goal will be to create complete solutions for individuals in the medical community. Our group has experience and success with the conceptualization, construction and financing of medical and dental clinic spaces. Vel-Cora Solutions will be established to accommodate all areas of the development and creation of clinics for medical professionals from building construction to equipment financing and administrations.

You can mention these companies and take photos from their websites. You can also use stock photos.

Our construction partner:
https://318bld.com/projects/

Our equipment leasing partner:
https://www.norvixa.com/

Our Management Team and medical partners

Gil Parish
https://www.ourfirmstance.ca/

Dietmar Vellasquin
https://www.gshdentalservices.com/about-us

PROPOSED PROJECTS (see attachment for details)
Pinegrove Business Park
Holtmere Business Park
Mt. Corwin Ridge Professional

Target Market(s)

Investors

Industry/Entity Type

Investment

Coding

Coded - Design and coding required

Number of Pages Required

4 page

Font styles to use
Sans Serif

Requirements
Must have
• Wordpress – must be both desktop and mobile friendly with fast page load speed
Ability to edit after ourselves in Wordpress
Attractive home page with logo etc.
Logo colours are: for the blue the pantone color is #0355a3
and for the green is #8cc63f

Sections, about us, what we do/services we provide, contact us

```html
<!DOCTYPE html>
<html lang="en">
<head>
<meta charset="utf-8">
<title>Contact Us – Vel-Cora Solutions</title>
<link rel="stylesheet" href="https://fonts.googleapis.com/css2?family=Montserrat:wght@600;700;800&family=Mulish:wght@400;600;700&family=Oswald:wght@600&display=swap">
<style>
:root{
  --blue:#0355a3;
  --green:#8cc63f;
  --black:#000;
  --ink:#2b2b2b;
  --muted:#666;
  --line:#cfd3d8;
  --footer:#232323;
  --white:#fff;
}
*{box-sizing:border-box;margin:0;padding:0}
html,body{width:882px;height:1200px;overflow:hidden;background:var(--white)}
body{position:relative;font-family:"Mulish",sans-serif;color:var(--ink)}
.abs{position:absolute}
svg{display:block}

/* top bar */
.topbar{left:0;top:0;width:882px;height:51px;background:var(--black)}
.top-contact{top:14px;display:flex;align-items:center;gap:7px;color:var(--white);font-size:11.5px;font-weight:600;letter-spacing:.3px}
.dot{width:23px;height:23px;border-radius:50%;background:var(--green);display:flex;align-items:center;justify-content:center}

/* nav */
.navbar{left:0;top:51px;width:882px;height:47px;background:var(--white)}
.nav-item{top:51px;height:47px;line-height:47px;font-family:"Montserrat",sans-serif;font-weight:700;font-size:11.2px;letter-spacing:.4px;color:#1d1d1d}
.nav-item.active{background:var(--blue);color:var(--white);padding:0 12px}

/* logo card */
.logo-card{left:96px;top:0;width:180px;height:128px;background:var(--white);border-radius:0 0 14px 14px;clip-path:polygon(0 0,100% 0,100% 86%,50% 100%,0 86%);box-shadow:0 4px 10px rgba(0,0,0,.15);display:flex;flex-direction:column;align-items:center;justify-content:center;padding-bottom:14px;z-index:3}
.brand-name{font-family:"Montserrat",sans-serif;font-weight:800;color:var(--blue);text-align:center;line-height:1}
.brand-square{width:16px;height:16px;background:var(--blue);margin-bottom:7px}

/* hero */
.hero{left:0;top:98px;width:882px;height:294px;background:linear-gradient(100deg,#4d7f97 0%,#2f5f7a 35%,#1c2e3c 62%,#4b8aa5 100%)}
.hero-title{left:94px;top:214px;font-family:"Oswald",sans-serif;font-weight:600;font-size:36px;color:var(--white);letter-spacing:.3px;text-shadow:0 2px 4px rgba(0,0,0,.35)}

/* section */
.section-title{left:0;top:456px;width:882px;text-align:center;font-family:"Montserrat",sans-serif;font-weight:800;font-size:25px;color:var(--blue);letter-spacing:.6px}
.section-title span{color:var(--green)}
.title-rule{left:425px;top:495px;width:32px;height:2px;background:#d5e3f1}
.col-heading{top:520px;font-family:"Montserrat",sans-serif;font-weight:700;font-size:20.5px;letter-spacing:1.2px;color:#222}

.field{left:97px;width:294px;height:29px;border:1px solid var(--line);border-radius:2px;padding:8px 8px;font-size:9.5px;color:var(--muted)}
.field b{color:#d9262c;font-weight:600}
.submit{left:97px;top:783px;width:94px;height:32px;background:var(--blue);color:var(--white);font-family:"Montserrat",sans-serif;font-weight:700;font-size:10px;letter-spacing:.5px;display:flex;align-items:center;justify-content:center;border-radius:2px}
.divider{left:423px;top:520px;width:1px;height:310px;background:linear-gradient(#fff,#e3e3e3 20%,#e3e3e3 80%,#fff)}

.map{left:445px;top:566px;width:341px;height:129px;border:1px solid #c9c9c9;background:linear-gradient(135deg,#f3eef3,#efe9ee)}
.info-icon{width:23px;height:23px;border-radius:50%;border:1px solid #e3e3e3;display:flex;align-items:center;justify-content:center}
.info-label{font-family:"Montserrat",sans-serif;font-weight:600;font-size:10px;color:#222;letter-spacing:.2px}
.info-text{font-size:10px;color:#333;margin-top:5px}

/* footer */
.footer{left:0;top:888px;width:882px;height:276px;background:var(--footer)}
.foot-heading{top:942px;font-family:"Montserrat",sans-serif;font-weight:700;font-size:11px;letter-spacing:.5px;color:var(--green)}
.foot-rule{top:966px;width:36px;height:1px;background:var(--green)}
.foot-divider{top:945px;width:1px;height:170px;background:#2f2f2f}
.quick-link{left:99px;font-size:10.5px;color:#eee}
.quick-link i{font-style:normal;font-size:8px;margin-right:4px}
.fc-icon{width:24px;height:24px;border-radius:50%;background:var(--blue);display:flex;align-items:center;justify-content:center}
.fc-label{font-family:"Montserrat",sans-serif;font-weight:600;font-size:10px;color:#fff}
.fc-text{font-size:10px;color:#eee;line-height:17px}
.social{left:475px;display:flex;align-items:center;gap:9px;font-size:10.5px;color:#eee}
.social .circ{width:24px;height:24px;border-radius:50%}
.copyright{left:0;top:1164px;width:882px;height:36px;background:var(--blue);color:#fff;font-size:10px;text-align:center;line-height:36px}
.copyright b{font-weight:700}
</style>
</head>
<body>

<header>
  <div class="abs topbar"></div>
  <div class="abs top-contact" style="left:484px">
    <span class="dot"><svg width="11" height="11" viewBox="0 0 24 24"><path fill="#fff" d="M6.6 10.8a15 15 0 0 0 6.6 6.6l2.2-2.2c.3-.3.7-.4 1-.2 1.1.4 2.3.6 3.6.6.6 0 1 .4 1 1V20c0 .6-.4 1-1 1A17 17 0 0 1 3 4c0-.6.4-1 1-1h3.5c.6 0 1 .4 1 1 0 1.3.2 2.5.6 3.6.1.3 0 .7-.2 1z"/></svg></span>
    780-555-0142
  </div>
  <div class="abs top-contact" style="left:615px">
    <span class="dot"><svg width="11" height="11" viewBox="0 0 24 24"><rect x="3" y="6" width="18" height="12" rx="1.5" fill="none" stroke="#fff" stroke-width="2"/><path d="M3 7l9 6 9-6" fill="none" stroke="#fff" stroke-width="2"/></svg></span>
    info@velcorahealth.ca
  </div>

  <div class="abs navbar"></div>
  <nav>
    <div class="abs nav-item" style="left:406px">HOME</div>
    <div class="abs nav-item" style="left:490px">ABOUT US</div>
    <div class="abs nav-item" style="left:589px">WHAT WE DO</div>
    <div class="abs nav-item active" style="left:687px">CONTACT US</div>
  </nav>

  <div class="abs logo-card">
    <div class="brand-square"></div>
    <div class="brand-name" style="font-size:22px">VEL-CORA</div>
    <div class="brand-name" style="font-size:13px;margin-top:4px;letter-spacing:1px">SOLUTIONS</div>
  </div>
</header>

<section>
  <div class="abs hero" role="img" aria-label="Photo of a businessman holding a smartphone with glowing contact icons above it"></div>
  <h1 class="abs hero-title">CONTACT US</h1>
</section>

<main>
  <h2 class="abs section-title">CONTACT <span>US</span></h2>
  <div class="abs title-rule"></div>

  <h3 class="abs col-heading" style="left:97px">HOW CAN WE HELP YOU?</h3>
  <div class="abs field" style="top:566px">Name <b>*</b></div>
  <div class="abs field" style="top:603px">Email <b>*</b></div>
  <div class="abs field" style="top:640px">Phone</div>
  <div class="abs field" style="top:678px;height:94px">Message</div>
  <div class="abs submit">SUBMIT</div>

  <div class="abs divider"></div>

  <h3 class="abs col-heading" style="left:446px">VEL-CORA SOLUTIONS</h3>
  <div class="abs map" role="img" aria-label="Street map showing the office location marked with a red pin"></div>

  <div class="abs info-icon" style="left:445px;top:716px"><svg width="10" height="12" viewBox="0 0 24 24"><path fill="#8cc63f" d="M12 2a7 7 0 0 0-7 7c0 5 7 13 7 13s7-8 7-13a7 7 0 0 0-7-7zm0 9.5A2.5 2.5 0 1 1 12 6.5a2.5 2.5 0 0 1 0 5z"/></svg></div>
  <div class="abs" style="left:477px;top:716px">
    <div class="info-label">VEL-CORA SOLUTIONS</div>
    <div class="info-text">#201, 9 Larchmont Road Sherwood Park, AB T8B 2K4</div>
  </div>

  <div class="abs info-icon" style="left:445px;top:763px"><svg width="10" height="10" viewBox="0 0 24 24"><path fill="#8cc63f" d="M6.6 10.8a15 15 0 0 0 6.6 6.6l2.2-2.2c.3-.3.7-.4 1-.2 1.1.4 2.3.6 3.6.6.6 0 1 .4 1 1V20c0 .6-.4 1-1 1A17 17 0 0 1 3 4c0-.6.4-1 1-1h3.5c.6 0 1 .4 1 1 0 1.3.2 2.5.6 3.6.1.3 0 .7-.2 1z"/></svg></div>
  <div class="abs" style="left:477px;top:763px">
    <div class="info-label">PHONE</div>
    <div class="info-text" style="margin-top:3px">780-555-0142</div>
  </div>

  <div class="abs info-icon" style="left:578px;top:763px"><svg width="10" height="10" viewBox="0 0 24 24"><path fill="#8cc63f" d="M3 6h18v12H3z"/><path d="M3 7l9 6 9-6" fill="none" stroke="#fff" stroke-width="2"/></svg></div>
  <div class="abs" style="left:610px;top:763px">
    <div class="info-label">EMAIL</div>
    <div class="info-text" style="margin-top:3px">info@velcorahealth.ca</div>
  </div>
</main>

<footer>
  <div class="abs footer"></div>

  <h4 class="abs foot-heading" style="left:99px">QUICK LINKS</h4>
  <div class="abs foot-rule" style="left:99px"></div>
  <div class="abs quick-link" style="top:978px"><i>&gt;&gt;</i>Home</div>
  <div class="abs quick-link" style="top:999px"><i>&gt;&gt;</i>About Us</div>
  <div class="abs quick-link" style="top:1020px"><i>&gt;&gt;</i>What We Do</div>
  <div class="abs quick-link" style="top:1041px"><i>&gt;&gt;</i>Contact Us</div>
  <div class="abs foot-divider" style="left:207px"></div>

  <h4 class="abs foot-heading" style="left:241px">CONTACT DETAILS</h4>
  <div class="abs foot-rule" style="left:241px"></div>
  <div class="abs fc-icon" style="left:243px;top:982px"><svg width="10" height="12" viewBox="0 0 24 24"><path fill="#fff" d="M12 2a7 7 0 0 0-7 7c0 5 7 13 7 13s7-8 7-13a7 7 0 0 0-7-7zm0 9.5A2.5 2.5 0 1 1 12 6.5a2.5 2.5 0 0 1 0 5z"/></svg></div>
  <div class="abs" style="left:276px;top:981px">
    <div class="fc-label">VEL-CORA SOLUTIONS</div>
    <div class="fc-text">#201, 9 Larchmont Road<br>Sherwood Park, AB T8B 2K4</div>
  </div>
  <div class="abs fc-icon" style="left:243px;top:1046px"><svg width="10" height="10" viewBox="0 0 24 24"><path fill="#fff" d="M6.6 10.8a15 15 0 0 0 6.6 6.6l2.2-2.2c.3-.3.7-.4 1-.2 1.1.4 2.3.6 3.6.6.6 0 1 .4 1 1V20c0 .6-.4 1-1 1A17 17 0 0 1 3 4c0-.6.4-1 1-1h3.5c.6 0 1 .4 1 1 0 1.3.2 2.5.6 3.6.1.3 0 .7-.2 1z"/></svg></div>
  <div class="abs" style="left:276px;top:1045px">
    <div class="fc-label">PHONE</div>
    <div class="fc-text">780-555-0142</div>
  </div>
  <div class="abs fc-icon" style="left:243px;top:1091px"><svg width="10" height="10" viewBox="0 0 24 24"><path fill="#fff" d="M3 6h18v12H3z"/><path d="M3 7l9 6 9-6" fill="none" stroke="#0355a3" stroke-width="2"/></svg></div>
  <div class="abs" style="left:276px;top:1090px">
    <div class="fc-label">EMAIL</div>
    <div class="fc-text">info@velcorahealth.ca</div>
  </div>
  <div class="abs foot-divider" style="left:439px"></div>

  <h4 class="abs foot-heading" style="left:473px">FOLLOW US ON</h4>
  <div class="abs foot-rule" style="left:473px"></div>
  <div class="abs social" style="top:982px"><span class="circ" style="background:#1877f2"></span>Pagebook</div>
  <div class="abs social" style="top:1017px"><span class="circ" style="background:#1da1f2"></span>Chirper</div>
  <div class="abs social" style="top:1052px"><span class="circ" style="background:#0a84c1"></span>Linkwork</div>
  <div class="abs social" style="top:1087px"><span class="circ" style="background:#d9141e"></span>Snapgram</div>
  <div class="abs foot-divider" style="left:599px"></div>

  <div class="abs" style="left:632px;top:985px;width:153px;display:flex;flex-direction:column;align-items:center">
    <div class="brand-square" style="width:22px;height:22px;margin-bottom:10px"></div>
    <div class="brand-name" style="font-size:27px">VEL-CORA</div>
    <div class="brand-name" style="font-size:15px;margin-top:5px;letter-spacing:1.5px">SOLUTIONS</div>
  </div>

  <div class="abs copyright">Copyright © 2020 <b>VEL-CORA SOLUTIONS</b>. All Rights Reserved.</div>
</footer>

</body>
</html>
```